KVB Website

We need a website for a company based in Doha Qatar called Brightpath Talent Global. It is a global recruitment company, that specializes in both mass recruitment and headhunting. The company is the number 1 one stop shop for recruitment in Qatar. It recruits from all over the world Europe, Asia, Americas, Middle East, Africa for Qatar.

Target Market(s)

Multinational companies, fortune 500 company CEO's, any top earning companies that are looking for a large number of employees or headhunting employees.
Also for candidates looking for companies to work in Qatar.

Industry/Entity Type

Shop

Colors
ffffff

Requirements
Must have
• Most important qualities the website needs to have:
Clean
Modern
Elegant
Professional
Less Tabs
Minimalisitc

Some examples, I would like you to follow are here:
http://www.velmora.ca/
http://www.trovenkip.com/
https://quelbrandix.com/match#

The main color should be white and it has to have a very stylish, modern and cool look. While being minimalistic. I do not want too many tabs. I want it to be simplistic to understand. the only place where the pink logo color is should be in the logo. The logo color should not be anywhere else. It has to be absolutely sleek. Please follow the example websites that I have provided.

I will send the contact details you need to add later. There is no need for a log in page.

Whatever you think that may be important for a recruitment site do suggest. But there is no need for a log in area as we are a different kind of recruitment company.

There should be an area for testimonials from clients. There should also be an area for news flash for the latest countries we are hiring from and the latest companies we are hiring for and the latest positions we are looking for.

Show me the best please. Whoever gives me the best, I will give them an order for the 2nd website too.

Nice to have
• I have included a powerpoint to explain more!

```html
<!DOCTYPE html>
<html lang="en">
<head>
<meta charset="utf-8">
<title>Brightpath Talent Global</title>
<link href="https://fonts.googleapis.com/css2?family=Raleway:wght@400;500;600;700&display=swap" rel="stylesheet">
<style>
:root{
  --brand:#a31d60;
  --accent:#333333;
  --accent-strong:#1f1f1f;
  --ink:#333333;
  --text:#6a6a6a;
  --nav:#3b3b3b;
  --panel:#ececec;
  --soft:#f4f4f4;
  --base:#2f2f2f;
  --white:#ffffff;
}
*{box-sizing:border-box;margin:0;padding:0}
html,body{width:1200px;height:2922px;overflow:hidden}
body{font-family:"Raleway",sans-serif;color:var(--text);background:var(--white);position:relative}
a{color:inherit;text-decoration:none}

.topbar{position:absolute;top:0;left:0;width:1200px;height:92px;background:var(--white)}
.job-search-box{position:absolute;right:36px;top:39px;width:380px;height:40px;border:1px solid #ddd;border-radius:3px;background:#f7f7f7;font-size:15px;color:#999;padding:10px 12px}
.job-search-box svg{position:absolute;right:12px;top:9px}

.main-nav{position:absolute;top:92px;left:0;width:1200px;height:52px;background:var(--nav);border-bottom:1px solid #222}
.main-nav ul{list-style:none;position:absolute;left:300px;top:0;display:flex;height:52px}
.main-nav li{color:#fff;font-size:14px;font-weight:600;padding:0 20px;line-height:52px;border-right:1px solid #2a2a2a}
.main-nav li.active{background:var(--accent-strong)}

.brand-badge{position:absolute;left:64px;top:0;width:215px;height:259px;background:var(--white);z-index:5;box-shadow:0 3px 8px rgba(0,0,0,.25);display:flex;flex-direction:column;align-items:center;padding-top:40px}
.brand-badge .mark{width:96px;height:96px;border-radius:50%;background:var(--brand)}
.brand-badge .name{margin-top:22px;text-align:center;color:var(--brand);font-weight:700;font-size:19px;line-height:23px}

.hero{position:absolute;top:144px;left:0;width:1200px;height:553px;background:linear-gradient(#e9e9e9,#d6d6d6);overflow:hidden;border-bottom:4px solid #cfcfcf}
.hero-map{position:absolute;left:300px;top:8px;width:860px;height:400px;background:radial-gradient(ellipse at center,#cfcfd3 0%,#d9d9dc 55%,rgba(233,233,233,0) 75%)}
.hero-team{position:absolute;left:458px;top:70px;width:516px;height:480px;background:linear-gradient(#5e5e66,#3b3b42);border-radius:6px 6px 0 0;opacity:.85}
.hero-title{position:absolute;left:68px;top:200px;color:#3a3a3a;font-size:31px;font-weight:500;line-height:38px;letter-spacing:.5px}
.hero-title strong{display:block;color:var(--accent-strong);font-weight:700;margin-top:8px}
.hero-arrows{position:absolute;left:66px;top:362px;display:flex;gap:10px}
.round-arrow{width:40px;height:40px;border-radius:50%;background:#4a4a4a;display:flex;align-items:center;justify-content:center}

.welcome{position:absolute;top:697px;left:0;width:1200px;height:380px;text-align:center}
.welcome h1{margin-top:75px;font-size:39px;font-weight:400;color:var(--ink)}
.welcome h1 span{font-weight:400}
.welcome p{width:848px;margin:24px auto 0;font-size:15.5px;line-height:24px;color:#777}
.btn{display:inline-block;background:var(--accent);color:#fff;font-weight:700;font-size:11.5px;letter-spacing:.3px;text-transform:uppercase;text-align:center}
.btn-block{width:132px;height:43px;line-height:43px;margin-top:33px}
.btn-pill{width:103px;height:31px;line-height:31px;border-radius:8px;font-size:10px}

.core-values{position:absolute;top:1077px;left:0;width:1200px;height:438px;background:var(--soft);text-align:center;box-shadow:inset 0 8px 10px -8px rgba(0,0,0,.15)}
.core-values h2{margin-top:34px;font-size:36px;font-weight:400;color:var(--ink)}
.value{position:absolute;top:112px;width:340px;text-align:center}
.value svg{height:94px}
.value h3{margin-top:22px;font-size:18px;font-weight:600;color:#333;letter-spacing:.5px}
.value p{margin:10px auto 0;width:320px;height:60px;overflow:hidden;font-size:14px;line-height:20px;color:#666}
.value .btn{margin-top:14px}

.info-panels{position:absolute;top:1553px;left:0;width:1200px;height:381px}
.panel{position:absolute;top:0;width:331px;height:381px;background:var(--panel)}
.panel-head{height:55px;background:var(--nav);color:#fff;font-size:18px;font-weight:600;line-height:55px;padding-left:22px;letter-spacing:.3px}
.news-item{display:flex;gap:12px;margin:20px 0 0 10px}
.news-item + .news-item{margin-top:26px}
.news-thumb{width:69px;height:69px;background:linear-gradient(#7f9bc0,#3a4f6f);flex:none}
.news-item h4{font-size:12.5px;font-weight:600;color:var(--accent)}
.news-item time{display:block;font-size:11px;color:#888;margin-top:3px}
.news-item p{font-size:12px;line-height:15px;color:#666;margin-top:4px}
.testimonial{padding:27px 30px 0;font-size:12.6px;line-height:20px;color:#666}
.testimonial cite{display:block;font-style:normal;color:var(--accent);font-weight:600;font-size:12.5px;margin-top:4px}
.square-arrows{position:absolute;left:34px;top:326px;display:flex;gap:12px}
.sq{width:22px;height:22px;background:#8a8a8a;display:flex;align-items:center;justify-content:center}
.gallery-photo{position:absolute;left:36px;top:84px;width:259px;height:220px;background:linear-gradient(135deg,#1a6fbf,#0d3f78)}
.gallery-arrow{position:absolute;top:176px;font-size:26px;color:#555}
.panel .btn-view{position:absolute;left:120px;top:322px;width:90px;height:33px;line-height:33px;font-size:11px}

.job-alerts{position:absolute;top:2016px;left:0;width:1200px;height:263px;background:var(--panel);text-align:center}
.job-alerts h2{margin-top:34px;font-size:36px;font-weight:400;color:var(--ink)}
.email-field{display:block;width:308px;height:45px;margin:22px auto 0;background:#fff;border:1px solid #ccc;text-align:left;padding:12px 15px;font-size:13px;font-style:italic;color:#aaa}
.btn-subscribe{width:168px;height:46px;line-height:46px;margin-top:20px;font-size:17px;font-weight:500}

.clients{position:absolute;top:2279px;left:0;width:1200px;height:201px;background:#fff}
.client-row{position:absolute;left:62px;top:58px;width:1076px;height:96px;display:flex;align-items:center;justify-content:space-between}
.client{display:flex;align-items:center;gap:10px;font-size:24px;font-weight:700;color:#5a5a5a}
.client i{width:26px;height:26px;border-radius:50%;background:#6a6a6a;display:block}
.client-arrow{position:absolute;top:80px;font-size:40px;color:#ccc}

.site-footer{position:absolute;top:2480px;left:0;width:1200px;height:335px;background:linear-gradient(#5f5f5f,#4e4e4e)}
.footer-col{position:absolute;top:38px}
.footer-col h5{color:#fff;font-size:17px;font-weight:600;letter-spacing:.5px}
.footer-col ul{list-style:none;margin-top:24px}
.footer-col li{color:#e5e5e5;font-size:13.5px;line-height:25px}
.footer-col address{font-style:normal;color:#e5e5e5;font-size:13.5px;line-height:25px;margin-top:24px}
.footer-brand{position:absolute;left:64px;top:198px;width:104px;text-align:center}
.footer-brand .mark{width:40px;height:40px;border-radius:50%;background:var(--brand);margin:0 auto}
.footer-brand .name{color:#fff;font-weight:700;font-size:11px;line-height:14px;margin-top:8px}

.base-bar{position:absolute;top:2815px;left:0;width:1200px;height:107px;background:var(--base)}
.copyright{position:absolute;left:74px;top:53px;font-size:13px;color:#8a8a8a}
.social{position:absolute;left:972px;top:43px;display:flex;gap:13px}
.social span{width:32px;height:32px;border-radius:50%;background:#8d8d8d;display:block}
</style>
</head>
<body>

<header class="topbar">
  <div class="job-search-box">Search Job
    <svg width="22" height="22" viewBox="0 0 22 22"><circle cx="9" cy="9" r="6.5" fill="none" stroke="#333" stroke-width="2.6"/><line x1="14" y1="14" x2="20" y2="20" stroke="#333" stroke-width="3" stroke-linecap="round"/></svg>
  </div>
</header>

<div class="brand-badge">
  <div class="mark"></div>
  <div class="name">BRIGHTPATH<br>TALENT GLOBAL</div>
</div>

<nav class="main-nav">
  <ul>
    <li class="active">HOME</li><li>ABOUT US</li><li>SERVICES</li><li>GALLERY</li><li>CAREER</li><li>NEWS</li><li>CLIENTS</li><li>JOB SEARCH</li>
  </ul>
</nav>

<section class="hero">
  <div class="hero-map" role="img" aria-label="Soft world map behind the team"></div>
  <div class="hero-team" role="img" aria-label="Photo of five business professionals standing in a row"></div>
  <h2 class="hero-title">QATAR’S LEADING<br>ONE-STOP-SHOP FOR<strong>GLOBAL RECRUITMENT</strong></h2>
  <div class="hero-arrows">
    <span class="round-arrow"><svg width="14" height="14" viewBox="0 0 14 14"><path d="M9 2 4 7l5 5" fill="none" stroke="#fff" stroke-width="2.5"/></svg></span>
    <span class="round-arrow"><svg width="14" height="14" viewBox="0 0 14 14"><path d="M5 2l5 5-5 5" fill="none" stroke="#fff" stroke-width="2.5"/></svg></span>
  </div>
</section>

<section class="welcome">
  <h1>Welcome to <span>Brightpath Talent Global</span></h1>
  <p>Brightpath Talent Global, popularly known as KVB, established in Doha, State of Qatar, is one of the pioneers of local and overseas recruitment along with manpower placements. It is our credibility and expertise in the business as proven by our experience and clients’ success, which makes us able and fully equipped to understand both the employer’s/employee’s needs and meet them with skill, commitment and efficiency.</p>
  <a class="btn btn-block">Read More</a>
</section>

<section class="core-values">
  <h2>Our Core Values</h2>
  <div class="value" style="left:60px">
    <svg viewBox="0 0 90 94" width="90"><g fill="var(--accent)"><circle cx="45" cy="12" r="9"/><rect x="35" y="24" width="20" height="40" rx="4"/><rect x="36" y="62" width="7" height="30"/><rect x="47" y="62" width="7" height="30"/><circle cx="16" cy="22" r="7"/><rect x="8" y="32" width="16" height="32" rx="3"/><rect x="9" y="62" width="6" height="24"/><rect x="17" y="62" width="6" height="24"/><circle cx="74" cy="22" r="7"/><rect x="66" y="32" width="16" height="32" rx="3"/><rect x="67" y="62" width="6" height="24"/><rect x="75" y="62" width="6" height="24"/></g></svg>
    <h3>PEOPLE</h3>
    <p>Our employees are efficient, motivated, honest, determined, result-driven and action-oriented. Their main focus is collaboration</p>
    <a class="btn btn-pill">Learn More</a>
  </div>
  <div class="value" style="left:440px">
    <svg viewBox="0 0 94 94" width="94"><g fill="var(--accent)"><g transform="translate(34 56)"><circle r="21"/><rect x="-6" y="-30" width="12" height="60"/><rect x="-30" y="-6" width="60" height="12"/><rect x="-6" y="-30" width="12" height="60" transform="rotate(45)"/><rect x="-6" y="-30" width="12" height="60" transform="rotate(-45)"/></g><g transform="translate(70 22)"><circle r="13"/><rect x="-4" y="-19" width="8" height="38"/><rect x="-19" y="-4" width="38" height="8"/><rect x="-4" y="-19" width="8" height="38" transform="rotate(45)"/><rect x="-4" y="-19" width="8" height="38" transform="rotate(-45)"/></g></g><circle cx="34" cy="56" r="8" fill="var(--soft)"/><circle cx="70" cy="22" r="5" fill="var(--soft)"/></svg>
    <h3>SERVICE</h3>
    <p>We aim for excellence through serving others and going above and beyond the call of duty. We deliver world-class service to every</p>
    <a class="btn btn-pill">Learn More</a>
  </div>
  <div class="value" style="left:808px">
    <svg viewBox="0 0 80 94" width="80"><g fill="var(--accent)"><rect x="2" y="60" width="10" height="28"/><rect x="16" y="52" width="10" height="36"/><rect x="30" y="44" width="10" height="44"/><rect x="44" y="36" width="10" height="52"/><rect x="58" y="28" width="10" height="60"/><path d="M2 50 60 14l-6-8 24-2-10 22-5-8L6 56z"/></g></svg>
    <h3>PERFORMANCE</h3>
    <p>This organization was started with the aim to excel in the field of recruitment. Hence, we are a high-performance organization,</p>
    <a class="btn btn-pill">Learn More</a>
  </div>
</section>

<section class="info-panels">
  <article class="panel" style="left:64px">
    <div class="panel-head">LATEST NEWS</div>
    <div class="news-item"><div class="news-thumb" role="img" aria-label="News photo of business people"></div><div><h4>Donec quam felis, ultricies</h4><time>24 Mar 2014</time><p>Ffelis, ultricies nec, pellentesque eu, pretium quis, sem</p></div></div>
    <div class="news-item"><div class="news-thumb" role="img" aria-label="News photo of a globe"></div><div><h4>Donec quam felis, ultricies</h4><time>24 Mar 2014</time><p>Ffelis, ultricies nec, pellentesque eu, pretium quis, sem</p></div></div>
    <div class="news-item"><div class="news-thumb" role="img" aria-label="News photo of a team"></div><div><h4>Donec quam felis, ultricies</h4><time>24 Mar 2014</time><p>Ffelis, ultricies nec, pellentesque eu, pretium quis, sem</p></div></div>
  </article>
  <article class="panel" style="left:434px">
    <div class="panel-head">TESTIMONIALS</div>
    <blockquote class="testimonial">Lorem ipsum dolor sit amet, consectetuer adipiscing elit. Aenean commodo ligula eget dolor. Aenean massa. Cum sociis natoque penatibus et magnis dis parturient montes, nascetur ridiculus mus. Donec quam felis, ultricies nec, pellentesque eu, pretium quis, sem. Nulla consequat massa quis enim. Donec pede justo, fringilla vel, aliquet nec,<cite>- Donec quam felis, ultricies</cite></blockquote>
    <div class="square-arrows">
      <span class="sq"><svg width="10" height="10" viewBox="0 0 10 10"><path d="M7 1 3 5l4 4" fill="none" stroke="#fff" stroke-width="2"/></svg></span>
      <span class="sq"><svg width="10" height="10" viewBox="0 0 10 10"><path d="M3 1l4 4-4 4" fill="none" stroke="#fff" stroke-width="2"/></svg></span>
    </div>
  </article>
  <article class="panel" style="left:806px">
    <div class="panel-head">PICTURE GALLERY</div>
    <span class="gallery-arrow" style="left:10px">‹</span>
    <div class="gallery-photo" role="img" aria-label="Gallery photo of a businesswoman with network icons"></div>
    <span class="gallery-arrow" style="right:10px">›</span>
    <a class="btn btn-view">View All</a>
  </article>
</section>

<section class="job-alerts">
  <h2>Sign up for Email Job Alerts</h2>
  <span class="email-field">Enter your Email Id</span>
  <a class="btn btn-subscribe">SUBSCRIBE</a>
</section>

<section class="clients">
  <span class="client-arrow" style="left:20px">‹</span>
  <div class="client-row">
    <span class="client"><i></i>CORVALIS</span>
    <span class="client">DUNMARRO</span>
    <span class="client"><i></i>Belqara</span>
    <span class="client">Tavisen</span>
    <span class="client"><i></i>ORLENT HARBOUR</span>
  </div>
  <span class="client-arrow" style="right:20px">›</span>
</section>

<footer class="site-footer">
  <div class="footer-col" style="left:64px"><h5>JOB SEEKER</h5><ul><li>New Candidate Signup</li><li>Search Jobs</li><li>Candidate Admin</li></ul></div>
  <div class="footer-col" style="left:362px"><h5>EMPLOYERS</h5><ul><li>New Employer Sign Up</li><li>Post A Job</li><li>Manage A Job</li><li>Update Information</li></ul></div>
  <div class="footer-col" style="left:639px"><h5>ABOUT KVB</h5><ul><li>About Us</li><li>Services</li><li>News</li><li>Featured Employer</li><li>Picture Gallery</li><li>Contact Us</li></ul></div>
  <div class="footer-col" style="left:904px"><h5>CONTACT US</h5>
    <address>Brightpath Talent Global<br>Office No: 210 &amp; 211, 2nd Floor,<br>Harbour Bldng. No: 8, Zone 12,<br>Al Noor Street, P.O. Box: 40550,<br>Doha, Qatar<br><br>Phone: +974 – 40001234<br>Fax: +97440005678<br>Email: info@brightpathtalent.com</address>
  </div>
  <div class="footer-brand"><div class="mark"></div><div class="name">BRIGHTPATH<br>TALENT GLOBAL</div></div>
</footer>

<div class="base-bar">
  <p class="copyright">All rights Reserved. Copyrights @ 2014</p>
  <div class="social"><span></span><span></span><span></span><span></span></div>
</div>

</body>
</html>
```